Nivel Crest - Powerpoint Templates

We are a consultancy to help builders to optimize their planning in order to save building costs. For that reason we need templates for teasers and presentations where we offer our services, show our team and their capacities and present workflows, organization charts, price lists etc.

```html
<!DOCTYPE html>
<html lang="en">
<head>
<meta charset="utf-8">
<title>Nivel Crest – Presentation Templates</title>
<link href="https://fonts.googleapis.com/css2?family=Audiowide&family=Poppins:wght@400;500;600;700&display=swap" rel="stylesheet">
<style>
  :root {
    --canvas-grey: #8b8787;
    --slide-bg: #f1f1f2;
    --slide-bg-soft: #fafafa;
    --gold: #c99e3c;
    --gold-light: #ecd08a;
    --gold-dark: #a97d24;
    --ink: #1d1d1f;
    --ink-soft: #555558;
    --steel-dark: #2f2f33;
    --steel-light: #8d8d92;
  }
  * { box-sizing: border-box; margin: 0; padding: 0; }
  html, body { width: 1200px; height: 4068px; overflow: hidden; }
  body { background: var(--canvas-grey); position: relative; font-family: "Poppins", sans-serif; color: var(--ink); }

  .slide {
    position: absolute; left: 24px; width: 1152px; height: 648px; overflow: hidden;
    background: linear-gradient(135deg, var(--slide-bg-soft) 0%, var(--slide-bg) 55%, #e9e9eb 100%);
  }
  .slide--cover { top: 16px; }
  .slide--about { top: 691px; }
  .slide--services { top: 1366px; }
  .slide--team { top: 2041px; }
  .slide--capacities { top: 2716px; }
  .slide--workflows { top: 3391px; }

  .header-band {
    position: absolute; top: 0; right: 0; width: 723px; height: 58px;
    background: linear-gradient(90deg, var(--gold-dark), var(--gold) 30%, var(--gold-light) 60%, var(--gold) 100%);
    clip-path: polygon(0 0, 100% 0, 100% 100%, 52px 100%);
  }
  .slide-title {
    position: absolute; top: 11px; font-family: "Audiowide", sans-serif; font-size: 31px;
    letter-spacing: 1px; color: var(--ink); text-transform: uppercase; line-height: 36px;
  }

  .brand-mini { position: absolute; left: 63px; top: 24px; display: flex; align-items: center; gap: 10px; }
  .brand-mini__square { width: 30px; height: 30px; background: var(--gold); }
  .brand-mini__name { font-family: "Poppins", sans-serif; font-weight: 600; font-size: 17px; color: var(--gold-dark); letter-spacing: 1px; }

  .cover-scene { position: absolute; inset: 0; }
  .cover-brand { position: absolute; left: 0; right: 0; top: 300px; display: flex; justify-content: center; align-items: center; gap: 24px; }
  .cover-brand__square { width: 64px; height: 64px; background: var(--gold); }
  .cover-brand__name { font-family: "Poppins", sans-serif; font-weight: 600; font-size: 64px; color: var(--gold); letter-spacing: 4px; }

  .lead { position: absolute; font-size: 14.5px; font-weight: 700; line-height: 26.5px; text-align: justify; }
  .body-copy { position: absolute; font-size: 14px; line-height: 28px; color: var(--ink-soft); text-align: justify; }
  .intro { position: absolute; left: 63px; top: 109px; width: 905px; font-size: 16.5px; line-height: 30px; }

  .service-card { position: absolute; top: 240px; width: 231px; height: 319px; color: #fff; text-align: center; }
  .service-card svg.card-shape { position: absolute; inset: 0; }
  .service-card__icon { position: absolute; left: 64px; top: 37px; width: 103px; height: 103px; }
  .service-card__title { position: absolute; left: 0; right: 0; top: 155px; font-family: "Audiowide", sans-serif; font-size: 17px; letter-spacing: 1px; }
  .service-card__text { position: absolute; left: 14px; right: 14px; top: 190px; font-size: 12.5px; line-height: 26px; }

  .member { position: absolute; top: 258px; width: 220px; text-align: center; }
  .member__photo { width: 177px; height: 177px; border-radius: 50%; margin: 0 auto; }
  .member__name { margin-top: 22px; font-family: "Audiowide", sans-serif; font-size: 17px; letter-spacing: 1.5px; }
  .member__role { margin-top: 4px; font-size: 16px; font-weight: 500; }

  .workflow-text { position: absolute; left: 63px; width: 480px; font-size: 15px; line-height: 30px; }
</style>
</head>
<body>

<section class="slide slide--cover">
  <svg class="cover-scene" width="1152" height="648" role="img" aria-label="Faint city skyline and businessman silhouette behind the title">
    <defs>
      <linearGradient id="coverGlow" x1="0" y1="1" x2="1" y2="0">
        <stop offset="0" stop-color="#dfe9ea"/>
        <stop offset="0.5" stop-color="#f3f3f4"/>
        <stop offset="1" stop-color="#f1dcdc"/>
      </linearGradient>
    </defs>
    <rect width="1152" height="648" fill="url(#coverGlow)"/>
  </svg>
  <div class="cover-brand">
    <span class="cover-brand__square"></span>
    <span class="cover-brand__name">NIVEL CREST</span>
  </div>
</section>

<section class="slide slide--about">
  <div class="header-band"></div>
  <h2 class="slide-title" style="left:614px">About us</h2>
  <div class="brand-mini"><span class="brand-mini__square"></span><span class="brand-mini__name">NIVEL CREST</span></div>
  <svg style="position:absolute;left:118px;top:107px" width="435" height="450" role="img" aria-label="Team of builders reviewing plans at a table, framed in a house outline">
    <defs>
      <linearGradient id="aboutPhoto" x1="0" y1="0" x2="1" y2="1">
        <stop offset="0" stop-color="#c9cdd2"/>
        <stop offset="0.6" stop-color="#8a8682"/>
        <stop offset="1" stop-color="#e4e4e4"/>
      </linearGradient>
    </defs>
    <polygon points="0,215 110,125 110,75 250,0 435,125 435,450 0,450" fill="url(#aboutPhoto)"/>
    <polyline points="8,450 8,218 118,130 118,80 250,8" fill="none" stroke="#444448" stroke-width="12"/>
    <polyline points="250,8 428,128 428,450 380,450" fill="none" stroke="var(--gold)" stroke-width="12"/>
  </svg>
  <p class="lead" style="left:614px;top:123px;width:434px">Lorem ipsum dolor sit amet, consectetur adipiscing elit, sed do eiusmod tempor incididunt ut labore et dolore magna aliqua. Quis ipsum suspendisse ultrices gravida. Risus commodo viverra maecenas accumsan lacus vel facilisis.</p>
  <p class="body-copy" style="left:614px;top:262px;width:452px">Sed ut perspiciatis unde omnis iste natus error sit voluptatem accusantium doloremque laudantium, totam rem aperiam, eaque ipsa quae ab illo inventore veritatis et quasi architecto beatae vitae dicta sunt explicabo. Nemo enim ipsam voluptatem quia voluptas sit aspernatur aut odit aut fugit, sed quia consequuntur magni dolores eos qui ratione voluptatem sequi nesciunt. Neque porro quisquam est, qui dolorem ipsum quia dolor sit amet, consectetur, adipisci velit, sed quia non numquam eius modi tempora incidunt ut labore et dolore magnam aliquam quaerat voluptatem.</p>
</section>

<section class="slide slide--services">
  <div class="header-band"></div>
  <h2 class="slide-title" style="left:614px">Our services</h2>
  <div class="brand-mini"><span class="brand-mini__square"></span><span class="brand-mini__name">NIVEL CREST</span></div>
  <p class="intro">Lorem ipsum dolor sit amet, consectetur adipiscing elit, sed do eiusmod tempor incididunt ut labore et dolore magna aliqua. Quis ipsum suspendisse ultrices gravida. Risus commodo viverra maecenas accumsan lacus vel facilisis.</p>

  <svg width="0" height="0" style="position:absolute">
    <defs>
      <linearGradient id="cardSteel" x1="0" y1="0" x2="0" y2="1">
        <stop offset="0" stop-color="#5d5d62"/>
        <stop offset="0.45" stop-color="var(--steel-dark)"/>
        <stop offset="1" stop-color="var(--steel-light)"/>
      </linearGradient>
      <linearGradient id="iconGold" x1="0" y1="0" x2="1" y2="1">
        <stop offset="0" stop-color="var(--gold-light)"/>
        <stop offset="1" stop-color="var(--gold-dark)"/>
      </linearGradient>
    </defs>
  </svg>

  <div class="service-card" style="left:58px">
    <svg class="card-shape" width="231" height="319"><polygon points="0,43 115.5,0 231,43 231,319 0,319" fill="url(#cardSteel)"/></svg>
    <svg class="service-card__icon" viewBox="0 0 100 100">
      <circle cx="50" cy="50" r="50" fill="url(#iconGold)"/>
      <rect x="46" y="24" width="26" height="17" rx="3" fill="#1d1d1f"/>
      <circle cx="36" cy="52" r="7" fill="#1d1d1f"/><path d="M24 74a12 12 0 0 1 24 0z" fill="#1d1d1f"/>
      <circle cx="64" cy="52" r="7" fill="#1d1d1f"/><path d="M52 74a12 12 0 0 1 24 0z" fill="#1d1d1f"/>
    </svg>
    <div class="service-card__title">LOREM IPSUM</div>
    <p class="service-card__text">Lorem ipsum dolor sit amet, consectetur adipiscing elit, sed do eiusmod tempor magna aliqua.</p>
  </div>
  <div class="service-card" style="left:325px">
    <svg class="card-shape" width="231" height="319"><polygon points="0,43 115.5,0 231,43 231,319 0,319" fill="url(#cardSteel)"/></svg>
    <svg class="service-card__icon" viewBox="0 0 100 100">
      <circle cx="50" cy="50" r="50" fill="url(#iconGold)"/>
      <path d="M32 42a18 18 0 0 1 36 0z" fill="#1d1d1f"/><rect x="28" y="42" width="44" height="5" fill="#1d1d1f"/>
      <circle cx="50" cy="55" r="9" fill="#1d1d1f"/><path d="M28 80a22 16 0 0 1 44 0z" fill="#1d1d1f"/>
    </svg>
    <div class="service-card__title">LOREM IPSUM</div>
    <p class="service-card__text">Lorem ipsum dolor sit amet, consectetur adipiscing elit, sed do eiusmod tempor magna aliqua.</p>
  </div>
  <div class="service-card" style="left:592px">
    <svg class="card-shape" width="231" height="319"><polygon points="0,43 115.5,0 231,43 231,319 0,319" fill="url(#cardSteel)"/></svg>
    <svg class="service-card__icon" viewBox="0 0 100 100">
      <circle cx="50" cy="50" r="50" fill="url(#iconGold)"/>
      <polyline points="24,48 38,38 50,44 68,26" fill="none" stroke="#1d1d1f" stroke-width="4"/>
      <circle cx="36" cy="58" r="7" fill="#1d1d1f"/><path d="M24 80a12 12 0 0 1 24 0z" fill="#1d1d1f"/>
      <circle cx="64" cy="64" r="12" fill="none" stroke="#1d1d1f" stroke-width="4"/>
    </svg>
    <div class="service-card__title">LOREM IPSUM</div>
    <p class="service-card__text">Lorem ipsum dolor sit amet, consectetur adipiscing elit, sed do eiusmod tempor magna aliqua.</p>
  </div>
  <div class="service-card" style="left:860px">
    <svg class="card-shape" width="231" height="319"><polygon points="0,43 115.5,0 231,43 231,319 0,319" fill="url(#cardSteel)"/></svg>
    <svg class="service-card__icon" viewBox="0 0 100 100">
      <circle cx="50" cy="50" r="50" fill="url(#iconGold)"/>
      <rect x="30" y="22" width="38" height="52" rx="3" fill="#1d1d1f"/>
      <polyline points="35,34 38,37 43,31" fill="none" stroke="var(--gold)" stroke-width="3"/><rect x="47" y="32" width="16" height="3" fill="var(--gold)"/>
      <polyline points="35,48 38,51 43,45" fill="none" stroke="var(--gold)" stroke-width="3"/><rect x="47" y="46" width="16" height="3" fill="var(--gold)"/>
      <circle cx="66" cy="68" r="10" fill="#1d1d1f" stroke="var(--gold)" stroke-width="2"/>
    </svg>
    <div class="service-card__title">LOREM IPSUM</div>
    <p class="service-card__text">Lorem ipsum dolor sit amet, consectetur adipiscing elit, sed do eiusmod tempor magna aliqua.</p>
  </div>
</section>

<section class="slide slide--team">
  <div class="header-band"></div>
  <h2 class="slide-title" style="left:614px">Our team</h2>
  <div class="brand-mini"><span class="brand-mini__square"></span><span class="brand-mini__name">NIVEL CREST</span></div>
  <p class="intro">Lorem ipsum dolor sit amet, consectetur adipiscing elit, sed do eiusmod tempor incididunt ut labore et dolore magna aliqua. Quis ipsum suspendisse ultrices gravida. Risus commodo viverra maecenas accumsan lacus vel facilisis.</p>
  <div class="member" style="left:84px">
    <div class="member__photo" role="img" aria-label="Portrait of Leonard, CEO" style="background:radial-gradient(circle at 50% 40%,#c7c9cb,#3d3f44)"></div>
    <div class="member__name">LEONARD</div><div class="member__role">CEO</div>
  </div>
  <div class="member" style="left:346px">
    <div class="member__photo" role="img" aria-label="Portrait of Clara, Co-CEO" style="background:radial-gradient(circle at 50% 40%,#d8c2a8,#2c2f38)"></div>
    <div class="member__name">CLARA</div><div class="member__role">CO - CEO</div>
  </div>
  <div class="member" style="left:607px">
    <div class="member__photo" role="img" aria-label="Portrait of Victor, builder in hard hat and safety vest" style="background:radial-gradient(circle at 50% 55%,#e88a3a,#5b5550)"></div>
    <div class="member__name">VICTOR</div><div class="member__role">Builders</div>
  </div>
  <div class="member" style="left:869px">
    <div class="member__photo" role="img" aria-label="Portrait of Matthias, engineer reviewing plans on site" style="background:radial-gradient(circle at 55% 55%,#d9dcc0,#3c4250)"></div>
    <div class="member__name">MATTHIAS</div><div class="member__role">Engineer</div>
  </div>
</section>

<section class="slide slide--capacities">
  <div class="header-band"></div>
  <h2 class="slide-title" style="left:614px">Capacities</h2>
  <div class="brand-mini"><span class="brand-mini__square"></span><span class="brand-mini__name">NIVEL CREST</span></div>
  <svg style="position:absolute;left:118px;top:155px" width="424" height="412" role="img" aria-label="Two builders in hard hats reviewing plans on a construction site">
    <defs>
      <linearGradient id="capPhoto" x1="0" y1="0" x2="1" y2="1">
        <stop offset="0" stop-color="#9fb2c4"/>
        <stop offset="0.55" stop-color="#e1873a"/>
        <stop offset="1" stop-color="#3b3f4a"/>
      </linearGradient>
    </defs>
    <circle cx="206" cy="206" r="204" fill="url(#capPhoto)"/>
    <path d="M206 2 A204 204 0 0 1 260 403" fill="none" stroke="var(--gold)" stroke-width="10"/>
  </svg>
  <p class="lead" style="left:613px;top:158px;width:455px;text-align:left;line-height:28.5px">Lorem ipsum dolor sit amet, consectetur adipiscing elit, sed do eiusmod tempor incididunt ut labore et dolore magna aliqua. Ut enim ad minim veniam, quis nostrud exercitation ullamco laboris nisi ut aliquip ex ea commodo consequat.</p>
  <p class="body-copy" style="left:613px;top:310px;width:518px;line-height:26.5px;font-size:13.5px">Sed ut perspiciatis unde omnis iste natus error sit voluptatem accusantium doloremque laudantium, totam rem aperiam, eaque ipsa quae ab illo inventore veritatis et quasi architecto beatae vitae dicta sunt explicabo. Nemo enim ipsam voluptatem quia voluptas sit aspernatur aut odit aut fugit, sed quia consequuntur magni dolores eos qui ratione voluptatem sequi nesciunt. Neque porro quisquam est, qui dolorem ipsum quia dolor sit amet, consectetur, adipisci velit, sed quia non numquam eius modi tempora incidunt ut labore et dolore magnam aliquam quaerat voluptatem.</p>
</section>

<section class="slide slide--workflows">
  <div class="header-band"></div>
  <h2 class="slide-title" style="left:513px">Workflows</h2>
  <div class="brand-mini"><span class="brand-mini__square"></span><span class="brand-mini__name">NIVEL CREST</span></div>
  <p class="workflow-text" style="top:171px">Sed ut perspiciatis unde omnis iste natus error sit voluptatem accusantium doloremque laudantium, totam rem aperiam, eaque ipsa quae ab illo inventore veritatis et quasi architecto beatae vitae dicta sunt explicabo.</p>
  <p class="workflow-text" style="top:310px">Sed ut perspiciatis unde omnis iste natus error sit voluptatem accusantium doloremque laudantium, totam rem aperiam, eaque ipsa quae ab illo inventore veritatis et quasi architecto beatae vitae dicta sunt explicabo.</p>
  <p class="workflow-text" style="top:451px">Sed ut perspiciatis unde omnis iste natus error sit voluptatem accusantium doloremque laudantium, totam rem aperiam, eaque ipsa quae ab illo inventore veritatis et quasi architecto beatae vitae dicta sunt explicabo.</p>
  <svg style="position:absolute;left:584px;top:178px" width="510" height="270" role="img" aria-label="Tablet with floating blue data charts showing workflow analytics">
    <defs>
      <linearGradient id="tabletGlow" x1="0" y1="0" x2="1" y2="1">
        <stop offset="0" stop-color="#dfe9f5"/>
        <stop offset="0.5" stop-color="#5d8fd0"/>
        <stop offset="1" stop-color="#e9eef5"/>
      </linearGradient>
    </defs>
    <polygon points="20,230 120,130 500,150 430,265" fill="#e3e5e8" stroke="#c2c5ca" stroke-width="4"/>
    <rect x="90" y="10" width="340" height="190" rx="10" fill="url(#tabletGlow)" opacity="0.85"/>
  </svg>
</section>

</body>
</html>
```